Four in One (Flexible infographic for Content Management Industry)

See attachment.
A graphic depicting 4 products, where each can stand on its own and each can be combined with others, but where, if all are taken together, the best result is achieved (the "super product").
Intended use is web. See attached file as an example.
The most basic idea is as the attached diagram shows, where 4 rectangles are arranged in a quadrangle, with a middle rectangle in the center representing the combined 4 products. This concept is fine except it is a bit too obvious as it stands. We are looking for either a variation of this or another concept.
The audience is technical + professional + enterprise - NOT consumers. Hence the design should be conservative in nature.
We are aware of tools like as Canva or Pictogram where such graphics are available, but we are looking for something with a bit more imagination and flexibility.
This graphic should be targeted to web sites and be delivered with vector-based (SVG) graphics.

```html
<!DOCTYPE html>
<html lang="en">
<head>
<meta charset="utf-8">
<title>Four in One – Super Product</title>
<link href="https://fonts.googleapis.com/css2?family=Montserrat:wght@600;700;800;900&display=swap" rel="stylesheet">
<style>
  :root {
    --frame-outer: #e6e6e6;
    --paper: #ffffff;
    --band: #e6e6e6;
    --ink: #111111;
    --docs: #52cca4;
    --security: #237b82;
    --erp: #3f5c9b;
    --digital: #1b365d;
    --ring: #0d0d0d;
  }
  html, body {
    margin: 0;
    padding: 0;
    width: 1155px;
    height: 1200px;
    overflow: hidden;
    background: var(--paper);
  }
  .infographic { display: block; width: 1155px; height: 1200px; }
  .sheet-border { fill: var(--frame-outer); }
  .sheet { fill: var(--paper); }
  .frame { fill: var(--paper); stroke-width: 24; stroke-linejoin: miter; }
  .frame--docs { stroke: var(--docs); }
  .frame--security { stroke: var(--security); }
  .frame--erp { stroke: var(--erp); }
  .frame--digital { stroke: var(--digital); }
  .title-band { fill: var(--band); }
  .card-title {
    font-family: 'Montserrat', sans-serif;
    font-weight: 700;
    font-size: 39px;
    fill: var(--ink);
  }
  .card-title--stacked { font-size: 35px; }
  .card-body {
    font-family: 'Montserrat', sans-serif;
    font-weight: 700;
    font-size: 18.5px;
    fill: var(--ink);
  }
  .feature {
    font-family: 'Montserrat', sans-serif;
    font-weight: 700;
    font-size: 19px;
    fill: var(--ink);
  }
  .tick { fill: none; stroke: var(--ink); stroke-width: 3.2; stroke-linecap: round; stroke-linejoin: round; }
  .hub-ring { fill: var(--ring); }
  .hub-core { fill: var(--band); }
  .hub-halo { fill: var(--paper); }
  .hub-title {
    font-family: 'Montserrat', sans-serif;
    font-weight: 900;
    font-size: 88px;
    letter-spacing: -2px;
    fill: var(--ink);
  }
  .badge--docs { fill: var(--docs); }
  .badge--security { fill: var(--security); }
  .badge--erp { fill: var(--erp); }
  .badge--digital { fill: var(--digital); }
  .glyph { fill: none; stroke: var(--paper); stroke-width: 3; stroke-linecap: round; stroke-linejoin: round; }
  .glyph-fill { fill: var(--paper); }
</style>
</head>
<body>
<svg class="infographic" viewBox="0 0 1605 1667" xmlns="http://www.w3.org/2000/svg" role="img" aria-label="Four products combining into one Super Product">
  <defs>
    <clipPath id="inner-docs"><path d="M754 784 L157 784 L157 387 A208 208 0 0 1 365 179 L754 179 Z"/></clipPath>
    <clipPath id="inner-security"><path d="M852 784 L852 179 L1240 179 A208 208 0 0 1 1448 387 L1448 784 Z"/></clipPath>
    <clipPath id="inner-erp"><path d="M754 884 L157 884 L157 1280 A208 208 0 0 0 365 1488 L754 1488 Z"/></clipPath>
    <clipPath id="inner-digital"><path d="M852 884 L1448 884 L1448 1280 A208 208 0 0 1 1240 1488 L852 1488 Z"/></clipPath>
    <symbol id="tick" viewBox="0 0 20 20"><path class="tick" d="M3 10.5 L8 15.5 L17 4.5"/></symbol>
  </defs>

  <rect class="sheet-border" x="0" y="0" width="1605" height="1667"/>
  <rect class="sheet" x="18" y="18" width="1569" height="1631"/>

  <!-- Document Management -->
  <g class="card card--docs">
    <path class="frame frame--docs" d="M766 796 L145 796 L145 387 A220 220 0 0 1 365 167 L766 167 Z"/>
    <rect class="title-band" x="150" y="265" width="610" height="85" clip-path="url(#inner-docs)"/>
    <text class="card-title" x="223" y="316">Document Management</text>
    <text class="card-body" x="192" y="411">
      <tspan x="192">Streamline document organization, access, and</tspan>
      <tspan x="192" dy="25.5">collaboration with easier file storage and sharing,</tspan>
      <tspan x="192" dy="25.5">leading to more efficient workflows .</tspan>
    </text>
    <use href="#tick" x="188" y="537" width="20" height="20"/>
    <use href="#tick" x="188" y="563" width="20" height="20"/>
    <use href="#tick" x="188" y="588" width="20" height="20"/>
    <use href="#tick" x="188" y="614" width="20" height="20"/>
    <text class="feature" x="216" y="551">Centralized Document Control</text>
    <text class="feature" x="216" y="577">Collaborative Workspace Integration</text>
    <text class="feature" x="216" y="602">Automated Compliance Tracking</text>
    <text class="feature" x="216" y="628">Check 4</text>
  </g>

  <!-- Security and Compliance -->
  <g class="card card--security">
    <path class="frame frame--security" d="M840 796 L840 167 L1240 167 A220 220 0 0 1 1460 387 L1460 796 Z"/>
    <rect class="title-band" x="846" y="265" width="610" height="85" clip-path="url(#inner-security)"/>
    <text class="card-title" x="878" y="313">Security and Compliance</text>
    <text class="card-body" x="883" y="412">
      <tspan x="883">Benefit from tailored cloud solutions, secure data</tspan>
      <tspan x="883" dy="25">storage, and expert disaster recovery planning for</tspan>
      <tspan x="883" dy="25">reliable and scalable IT operations.</tspan>
    </text>
    <use href="#tick" x="1041" y="527" width="20" height="20"/>
    <use href="#tick" x="1041" y="553" width="20" height="20"/>
    <use href="#tick" x="1041" y="578" width="20" height="20"/>
    <use href="#tick" x="1041" y="604" width="20" height="20"/>
    <text class="feature" x="1083" y="541">Custom Cloud Solutions</text>
    <text class="feature" x="1083" y="567">Secure Data Storage</text>
    <text class="feature" x="1083" y="592">Expert Disaster Recovery</text>
    <text class="feature" x="1083" y="618">Check 4</text>
  </g>

  <!-- Enterprise Resource Planning -->
  <g class="card card--erp">
    <path class="frame frame--erp" d="M766 872 L145 872 L145 1280 A220 220 0 0 0 365 1500 L766 1500 Z"/>
    <rect class="title-band" x="150" y="971" width="440" height="85" clip-path="url(#inner-erp)"/>
    <text class="card-title card-title--stacked" x="180" y="1010">
      <tspan x="180">Enterprise</tspan>
      <tspan x="180" dy="35">Resource Planning</tspan>
    </text>
    <text class="card-body" x="187" y="1141">
      <tspan x="187">Simplify management across finance, sales, and</tspan>
      <tspan x="187" dy="25.5">operations, enabling better decision-making</tspan>
      <tspan x="187" dy="25.5">and improved productivity.</tspan>
    </text>
    <use href="#tick" x="231" y="1274" width="20" height="20"/>
    <use href="#tick" x="231" y="1300" width="20" height="20"/>
    <use href="#tick" x="231" y="1325" width="20" height="20"/>
    <use href="#tick" x="231" y="1351" width="20" height="20"/>
    <text class="feature" x="264" y="1288">Integrated Business Processes</text>
    <text class="feature" x="264" y="1314">Enhanced Decision-Making</text>
    <text class="feature" x="264" y="1339">Productivity Improvement</text>
    <text class="feature" x="264" y="1365">Check 4</text>
  </g>

  <!-- Digital Transformation -->
  <g class="card card--digital">
    <path class="frame frame--digital" d="M840 872 L1460 872 L1460 1280 A220 220 0 0 1 1240 1500 L840 1500 Z"/>
    <rect class="title-band" x="1020" y="971" width="436" height="85" clip-path="url(#inner-digital)"/>
    <text class="card-title card-title--stacked" x="1072" y="1006">
      <tspan x="1072">Digital</tspan>
      <tspan x="1072" dy="37">Transformation</tspan>
    </text>
    <text class="card-body" x="894" y="1131">
      <tspan x="894">Turn scanned documents into easily searchable</tspan>
      <tspan x="894" dy="25.5">digital archives, boosting efficiency and</tspan>
      <tspan x="894" dy="25.5">accessibility.</tspan>
    </text>
    <use href="#tick" x="901" y="1274" width="20" height="20"/>
    <use href="#tick" x="901" y="1300" width="20" height="20"/>
    <use href="#tick" x="901" y="1325" width="20" height="20"/>
    <use href="#tick" x="901" y="1351" width="20" height="20"/>
    <text class="feature" x="943" y="1288">Instant searchable Archives with OCR</text>
    <text class="feature" x="943" y="1314">Automated Document Classification</text>
    <text class="feature" x="943" y="1339">DocuVault and Cloud Blob Ready</text>
    <text class="feature" x="943" y="1365">Check 4</text>
  </g>

  <!-- Central hub -->
  <g class="hub">
    <circle class="hub-ring" cx="805" cy="835" r="240"/>
    <circle class="hub-core" cx="805" cy="835" r="224"/>
    <circle class="hub-halo" cx="640" cy="668" r="84"/>
    <circle class="hub-halo" cx="971" cy="668" r="84"/>
    <circle class="hub-halo" cx="640" cy="999" r="84"/>
    <circle class="hub-halo" cx="971" cy="999" r="84"/>
    <text class="hub-title" x="810" y="812" text-anchor="middle">Super</text>
    <text class="hub-title" x="807" y="893" text-anchor="middle">Product</text>
  </g>

  <!-- Product badges -->
  <g class="badge">
    <circle class="badge--docs" cx="640" cy="668" r="57"/>
    <path class="glyph" d="M618 637 L648 637 L662 651 L662 697 L618 697 Z M648 637 L648 651 L662 651"/>
    <path class="glyph" d="M626 659 L654 659 M626 667 L654 667 M626 675 L654 675 M626 683 L654 683"/>
  </g>
  <g class="badge">
    <circle class="badge--security" cx="971" cy="668" r="57"/>
    <path class="glyph" d="M971 634 L998 645 L998 668 C998 686 986 698 971 704 C956 698 944 686 944 668 L944 645 Z"/>
    <circle class="glyph" cx="971" cy="670" r="17"/>
    <path class="glyph" d="M963 670 L969 676 L980 663"/>
  </g>
  <g class="badge">
    <circle class="badge--erp" cx="640" cy="999" r="57"/>
    <path class="glyph" d="M626 978 L626 1018 L660 1018 L660 978 M622 974 L654 974"/>
    <path class="glyph" d="M620 974 L620 1012 L656 1012 L656 974 Z"/>
    <path class="glyph" d="M627 983 L649 983 M627 990 L649 990 M627 997 L649 997 M627 1004 L649 1004"/>
  </g>
  <g class="badge">
    <circle class="badge--digital" cx="971" cy="999" r="57"/>
    <path class="glyph" d="M937 989 A48 48 0 0 1 1005 989" stroke-width="7"/>
    <path class="glyph" d="M949 1001 A31 31 0 0 1 993 1001" stroke-width="7"/>
    <circle class="glyph-fill" cx="971" cy="1019" r="8"/>
  </g>
</svg>
</body>
</html>
```